We need a web page design for a new company called "Brambel". We provide an innovative music sharing mobile application that allows music listeners to share their music without paying for a monthly subscription. We would like to incorporate the attached logo and color scheme. The final design should communicate music gifting and sharing.

Industry/Entity Type

It Company

```html
<!DOCTYPE html>
<html lang="en">
<head>
<meta charset="utf-8">
<title>Brambel</title>
<link href="https://fonts.googleapis.com/css2?family=Arvo:wght@700&family=Lato:wght@400;700;900&display=swap" rel="stylesheet">
<style>
:root{
  --green:#5aa400;
  --green-dark:#4a8a00;
  --ink:#222;
  --text:#555;
  --muted:#8a8a8a;
  --dark:#1e1e1e;
  --white:#fff;
}
*{margin:0;padding:0;box-sizing:border-box}
html,body{width:1200px;height:2981px;overflow:hidden}
body{font-family:"Lato",Arial,sans-serif;color:var(--text);background:var(--white);position:relative}
.abs{position:absolute}
section,header,footer{position:absolute;left:0;width:1200px;overflow:hidden}
.fill{position:absolute}

/* header */
.site-header{top:0;height:94px;background:var(--green)}
.brand{position:absolute;left:132px;top:0;height:94px;display:flex;align-items:center;color:var(--white)}
.brand-name{font-weight:900;font-size:44px;line-height:1}
.nav{position:absolute;top:0;left:549px;height:94px;display:flex;list-style:none}
.nav li{height:94px;line-height:94px;font-size:15px;color:var(--white);padding:0 16px}
.nav li.active{background:var(--white);color:var(--green);padding:0 18px}
.nav .caret{font-size:10px;margin-left:6px}

/* hero */
.hero{top:94px;height:532px}
.hero-bg{left:0;top:0;width:1200px;height:532px;background:radial-gradient(ellipse at 55% 40%,#5c5c5c 0%,#2c2c2c 45%,#121212 100%)}
.hero-device{left:745px;top:60px;width:300px;height:422px;border-radius:34px;background:linear-gradient(160deg,#3a3a3a,#111)}
.hero-device .screen{position:absolute;left:28px;top:62px;width:208px;height:300px;background:var(--green);border-radius:4px}
.hero-title{left:132px;top:148px;font-family:"Arvo",Georgia,serif;font-size:41px;color:var(--white)}
.hero-sub{left:132px;top:207px;font-weight:700;font-size:17px;line-height:30px;color:var(--white)}
.btn-now{left:132px;top:284px;width:151px;height:50px;background:var(--green);color:var(--white);font-weight:900;font-size:19px;display:flex;align-items:center;justify-content:center}

/* shared section title */
.section-title{position:absolute;left:0;width:1200px;text-align:center;font-weight:700;font-size:29px;color:var(--ink)}
.divider{position:absolute;left:500px;width:200px;height:14px}

/* welcome */
.welcome{top:626px;height:417px}
.welcome-visual{left:129px;top:144px;width:450px;height:224px;border-radius:18px;background:linear-gradient(135deg,#f1f1f1,#cfcfcf)}
.welcome-copy{left:628px;top:130px;width:440px;font-size:13.4px;line-height:24px}
.more{color:var(--green);font-weight:700}
.stat{position:absolute;width:120px;text-align:center}
.stat .ico{width:60px;height:60px;border-radius:50%;background:var(--green);margin:0 auto}
.stat .num{font-weight:700;font-size:19px;color:var(--ink);margin-top:12px}
.stat .lbl{font-size:11.5px;color:var(--muted);letter-spacing:.5px;margin-top:2px}

/* features */
.features{top:1043px;height:365px}
.features-bg{left:0;top:0;width:1200px;height:365px;background:radial-gradient(ellipse at 55% 50%,#565656 0%,#2a2a2a 55%,#151515 100%)}
.features .section-title{top:57px;color:var(--white)}
.feature{position:absolute;top:132px;width:180px;text-align:center;color:var(--white);font-weight:700;font-size:18px;line-height:32px}
.feature svg{display:block;margin:0 auto 16px}

/* how it works */
.how{top:1408px;height:691px}
.how-visual{left:149px;top:120px;width:447px;height:571px;border-radius:40px 40px 0 0;background:linear-gradient(170deg,#e8e8e8 0%,#2c2c2c 40%,#5aa400 90%)}
.how-intro{left:628px;top:135px;width:442px;font-size:13.4px;line-height:22px}
.step{position:absolute;left:633px;width:450px;height:100px}
.step .circle{position:absolute;left:0;top:0;width:82px;height:82px;border-radius:50%;background:var(--green);border:6px solid #e3efd3}
.step h3{position:absolute;left:105px;top:-8px;font-size:17px;color:var(--ink)}
.step p{position:absolute;left:105px;top:20px;width:340px;font-size:13.4px;line-height:22px}

/* reviews */
.reviews{top:2099px;height:298px}
.reviews-bg{left:0;top:0;width:1200px;height:298px;background:linear-gradient(180deg,#9a9a9a 0%,#cfcfcf 45%,#e2e2e2 100%)}
.reviews .section-title{top:58px}
.reviews-lead{left:0;width:1200px;top:128px;text-align:center;font-size:13.4px;color:#444}
.avatar{left:264px;top:171px;width:74px;height:74px;border-radius:50%;background:#b8b8b8;border:3px solid var(--white)}
.review-name{left:358px;top:168px;font-weight:700;font-size:15px;color:var(--ink)}
.review-text{left:358px;top:200px;width:580px;font-size:13.4px;line-height:24px;color:#333}
.arrow{top:196px}

/* contact */
.contact{top:2397px;height:452px}
.contact-bg{left:0;top:0;width:1200px;height:452px;background:radial-gradient(ellipse at 50% 45%,#4a4a4a 0%,#303030 60%,#242424 100%)}
.contact h2{position:absolute;top:58px;font-weight:400;font-size:29px;color:var(--white)}
.contact .lead{position:absolute;top:100px;font-size:13.4px;line-height:24px;color:var(--white)}
.field{position:absolute;top:177px;height:33px;background:var(--white);font-size:11px;color:#777;padding:9px 10px}
.field.area{top:243px;height:88px}
.btn-submit{left:132px;top:360px;width:106px;height:38px;border:2px solid var(--white);color:var(--white);font-weight:700;font-size:16px;display:flex;align-items:center;justify-content:center;letter-spacing:1px}
.social{position:absolute;left:793px;display:flex;align-items:center;gap:16px;color:var(--white);font-size:13.4px}
.social .ring{width:54px;height:54px;border-radius:50%;border:2px solid var(--white)}

/* footer */
.site-footer{top:2849px;height:95px;background:var(--green);color:var(--white);font-size:12.5px}
.foot-addr{left:154px;top:19px;line-height:20px}
.foot-contact{left:383px;top:20px;line-height:22px}
.foot-ico{position:absolute}
.foot-brand{position:absolute;left:880px;top:0;height:95px;display:flex;align-items:center}
.foot-brand .brand-name{font-size:40px;color:var(--white)}
.copyright{top:2944px;height:37px;background:#151515;color:#bbb;font-size:12.5px;text-align:center;line-height:37px}
</style>
</head>
<body>

<header class="site-header">
  <div class="brand"><span class="brand-name">Brambel</span></div>
  <ul class="nav">
    <li class="active">Home</li>
    <li>About<span class="caret">▼</span></li>
    <li>How It Work</li>
    <li>Download<span class="caret">▼</span></li>
    <li>Join</li>
    <li>Contact</li>
  </ul>
</header>

<section class="hero">
  <div class="fill hero-bg" role="img" aria-label="Dark photograph of a studio microphone and mixing desk"></div>
  <div class="fill hero-device" role="img" aria-label="Hand holding a smartphone showing the app download screen"><div class="screen"></div></div>
  <h1 class="abs hero-title">Get Brambel Music App Free</h1>
  <p class="abs hero-sub">We Provide Best Innovative Music Sharing<br>Mobile Application</p>
  <div class="abs btn-now">NOW!</div>
</section>

<section class="welcome">
  <h2 class="section-title" style="top:58px">Welcome to Brambel</h2>
  <svg class="divider" style="top:100px" viewBox="0 0 200 14"><line x1="0" y1="9" x2="200" y2="9" stroke="#ddd"/><circle cx="100" cy="9" r="4" fill="#888"/></svg>
  <div class="fill welcome-visual" role="img" aria-label="Tablet displaying the music player"></div>
  <p class="abs welcome-copy">Lorem ipsum dolor sit amet, consectetuer adipiscing elit, sed diam nonummy nibh euismod tincidunt ut laoreet dolore magna aliquam erat volutpat. Ut wisi enim ad minim veniam, quis nostrud exerci tation ullamcorper suscipit lobortis nisl ut aliquip ex ea commodo consequat...<span class="more">READ MORE&gt;&gt;</span></p>
  <div class="stat" style="left:618px;top:262px"><div class="ico"></div><div class="num">9920</div><div class="lbl">DOWNLOADS</div></div>
  <div class="stat" style="left:747px;top:262px"><div class="ico"></div><div class="num">999</div><div class="lbl">ROBO USER</div></div>
  <div class="stat" style="left:867px;top:262px"><div class="ico"></div><div class="num">938</div><div class="lbl">POMME USER</div></div>
  <div class="stat" style="left:976px;top:262px"><div class="ico"></div><div class="num">738</div><div class="lbl">BERRY USER</div></div>
</section>

<section class="features">
  <div class="fill features-bg" role="img" aria-label="Dark photograph of studio headphones"></div>
  <h2 class="section-title">Features and benefits</h2>
  <svg class="divider" style="top:100px" viewBox="0 0 200 14"><line x1="0" y1="9" x2="200" y2="9" stroke="#666"/><circle cx="100" cy="9" r="4" fill="#fff"/></svg>
  <div class="feature" style="left:119px"><svg width="108" height="108" viewBox="0 0 108 108"><circle cx="54" cy="54" r="52" fill="none" stroke="#fff" stroke-width="3"/><circle cx="54" cy="54" r="42" fill="#fff" fill-opacity=".15"/><circle cx="54" cy="54" r="20" fill="none" stroke="#fff" stroke-width="5"/><line x1="40" y1="68" x2="68" y2="40" stroke="#fff" stroke-width="5"/></svg>No Credit<br>Card Required</div>
  <div class="feature" style="left:312px"><svg width="108" height="108" viewBox="0 0 108 108"><circle cx="54" cy="54" r="52" fill="none" stroke="#fff" stroke-width="3"/><circle cx="54" cy="54" r="42" fill="#fff" fill-opacity=".15"/><rect x="38" y="50" width="32" height="26" rx="3" fill="#fff"/><path d="M44 50v-8a10 10 0 0 1 20 0" fill="none" stroke="#fff" stroke-width="5"/></svg>Unlimited<br>Access</div>
  <div class="feature" style="left:509px"><svg width="108" height="108" viewBox="0 0 108 108"><circle cx="54" cy="54" r="52" fill="none" stroke="#fff" stroke-width="3"/><circle cx="54" cy="54" r="42" fill="#fff" fill-opacity=".15"/><rect x="36" y="56" width="7" height="20" fill="#fff"/><rect x="47" y="42" width="7" height="34" fill="#fff"/><rect x="58" y="48" width="7" height="28" fill="#fff"/><rect x="69" y="36" width="7" height="40" fill="#fff"/></svg>Productivity<br>Tracker</div>
  <div class="feature" style="left:702px"><svg width="108" height="108" viewBox="0 0 108 108"><circle cx="54" cy="54" r="52" fill="none" stroke="#fff" stroke-width="3"/><circle cx="54" cy="54" r="42" fill="#fff" fill-opacity=".15"/><circle cx="54" cy="56" r="20" fill="none" stroke="#fff" stroke-width="4"/><path d="M50 48v14M50 48l10 -3v14" fill="none" stroke="#fff" stroke-width="3"/><circle cx="48" cy="63" r="3" fill="#fff"/><circle cx="58" cy="60" r="3" fill="#fff"/></svg>Multiple<br>Music Channels</div>
  <div class="feature" style="left:899px"><svg width="108" height="108" viewBox="0 0 108 108"><circle cx="54" cy="54" r="52" fill="none" stroke="#fff" stroke-width="3"/><circle cx="54" cy="54" r="42" fill="#fff" fill-opacity=".15"/><rect x="38" y="40" width="26" height="30" rx="3" fill="none" stroke="#fff" stroke-width="4"/><path d="M56 55h18M68 49l6 6-6 6" fill="none" stroke="#fff" stroke-width="4"/></svg>Social<br>Share</div>
</section>

<section class="how">
  <h2 class="section-title" style="top:55px">How It Works</h2>
  <svg class="divider" style="top:98px" viewBox="0 0 200 14"><line x1="0" y1="9" x2="200" y2="9" stroke="#ddd"/><circle cx="100" cy="9" r="4" fill="#888"/></svg>
  <div class="fill how-visual" role="img" aria-label="Hand holding a tablet showing the playlist screen"></div>
  <p class="abs how-intro">Lorem ipsum dolor sit amet, consectetur adipiscing elit. Pellentesque sed finibus lectus. Ut in sapien id n rutrum lacinia id nec tellus. Etiam tempor leo eu vulputa auctor. In feugiat sollicitudin enim sit amet volutpat.</p>
  <div class="step" style="top:240px"><div class="circle"></div><h3>Install Apps</h3><p>Lorem ipsum dolor sit amet, consectetur adipiscing elit. Pellentesque sed finibus lectus.<br><span class="more">READ MORE&gt;&gt;</span></p></div>
  <div class="step" style="top:376px"><div class="circle"></div><h3>Store Your Track</h3><p>Lorem ipsum dolor sit amet, consectetur adipiscing elit. Pellentesque sed finibus lectus.<br><span class="more">READ MORE&gt;&gt;</span></p></div>
  <div class="step" style="top:512px"><div class="circle"></div><h3>Play Your Track</h3><p>Lorem ipsum dolor sit amet, consectetur adipiscing elit. Pellentesque sed finibus lectus.<br><span class="more">READ MORE&gt;&gt;</span></p></div>
</section>

<section class="reviews">
  <div class="fill reviews-bg" role="img" aria-label="Faded photograph of a concert crowd"></div>
  <h2 class="section-title">App Reviews</h2>
  <svg class="divider" style="top:100px" viewBox="0 0 200 14"><line x1="0" y1="9" x2="200" y2="9" stroke="#bbb"/><circle cx="100" cy="9" r="4" fill="#666"/></svg>
  <p class="abs reviews-lead">Enim ad mini quis notrud exercitation ullamco laboris nisi ut aliqoido consequin reprehenderit.</p>
  <div class="fill avatar" role="img" aria-label="Reviewer portrait"></div>
  <div class="abs review-name">Culpa qui officia deserunt mollitlorum.</div>
  <p class="abs review-text">Enim ad mini quis notrud exercitation ullaco laboris nisi ut aliqoido consequin reprehenderit in voluptate velit essle cillum dolore.</p>
  <svg class="abs arrow" style="left:131px" width="16" height="22" viewBox="0 0 16 22"><path d="M13 2 3 11l10 9" fill="none" stroke="#222" stroke-width="3"/></svg>
  <svg class="abs arrow" style="left:1055px" width="16" height="22" viewBox="0 0 16 22"><path d="m3 2 10 9-10 9" fill="none" stroke="#222" stroke-width="3"/></svg>
</section>

<section class="contact">
  <div class="fill contact-bg" role="img" aria-label="Dark street map background"></div>
  <h2 style="left:132px">Contact Us</h2>
  <p class="lead" style="left:132px;width:610px">Lorem Ipsum is simply dummy text of the printing and typesetting industry. Lorem Ipsum has b industry's standard dummy text ever since the 1500s.</p>
  <div class="field" style="left:132px;width:196px">First and Last Name</div>
  <div class="field" style="left:335px;width:194px">Phone</div>
  <div class="field" style="left:537px;width:198px">Email id</div>
  <div class="field area" style="left:132px;width:603px">Type Here</div>
  <div class="abs btn-submit">SUBMIT</div>
  <h2 style="left:795px">Share With Us</h2>
  <p class="lead" style="left:795px;width:290px;font-size:12.5px;line-height:22px">Lorem Ipsum is simply dummy text of t printing and typesetting industry.</p>
  <div class="social" style="top:152px"><span class="ring"></span>Facelane</div>
  <div class="social" style="top:221px"><span class="ring"></span>Chirper</div>
  <div class="social" style="top:289px"><span class="ring"></span>Linkfolio</div>
  <div class="social" style="top:353px"><span class="ring"></span>Email</div>
</section>

<footer class="site-footer">
  <svg class="foot-ico" style="left:132px;top:20px" width="14" height="20" viewBox="0 0 14 20"><path d="M7 0a7 7 0 0 0-7 7c0 5 7 13 7 13s7-8 7-13a7 7 0 0 0-7-7z" fill="#fff"/><circle cx="7" cy="7" r="2.5" fill="#5aa400"/></svg>
  <p class="abs foot-addr">Contrary to popular belief,<br>Lorem Ipsum is<br>1234567</p>
  <svg class="foot-ico" style="left:355px;top:24px" width="14" height="14" viewBox="0 0 14 14"><path d="M3 0l3 3-2 2c1 2 3 4 5 5l2-2 3 3-2 3C6 14 0 8 0 3z" fill="#fff"/></svg>
  <svg class="foot-ico" style="left:355px;top:46px" width="14" height="14" viewBox="0 0 14 14"><rect x="1" y="5" width="12" height="7" fill="#fff"/><rect x="3" y="1" width="8" height="4" fill="#fff"/></svg>
  <svg class="foot-ico" style="left:355px;top:69px" width="14" height="12" viewBox="0 0 14 12"><rect width="14" height="12" fill="#fff"/><path d="M0 0l7 6 7-6" fill="none" stroke="#5aa400" stroke-width="1.5"/></svg>
  <p class="abs foot-contact">Phone: 555 010 2030<br>Fax: 555 010 2030<br>hello@brambelmusic.net</p>
  <div class="foot-brand"><span class="brand-name">Brambel</span></div>
</footer>

<div class="abs copyright" style="left:0;width:1200px">Copyright © 2014 Brambelmusic. All Rights Reserved.</div>

</body>
</html>
```